Need help in designing new business card utilizing our new logo.

BuildMark Solutions works with Construction Business Owners, Managers & IT Professionals to strengthen software usage and increase user productivity.

Our Construction Accounting and Mobile Field Management Software Clients engage with us in the following areas:

New Software Implementations
Software Re-Implementations
Redesigning Software Usage at the User Level
Project Coordination & Management
Continued Software Support

Old tag line:
Planning Ahead - Building Better Systems

www.buildmark-solutions.example

Ridge 4 is a product, but not needed for a new business card.

```html
<!DOCTYPE html>
<html lang="en">
<head>
<meta charset="utf-8">
<title>BuildMark Solutions – Business Card</title>
<link rel="stylesheet" href="https://fonts.googleapis.com/css2?family=Roboto:wght@400;500;700&family=Roboto+Condensed:wght@700&display=swap">
<style>
  :root {
    --brand-blue: #0f1fa6;
    --silver: #c4c4c4;
    --silver-light: #d9d9d9;
    --paper: #f4f4f4;
    --ink: #1e1e1e;
    --ink-soft: #3a3a3a;
    --rule: #a9a9a9;
    --backdrop: #b9b9b9;
    --white: #ffffff;
  }
  * { box-sizing: border-box; margin: 0; padding: 0; }
  html, body { width: 1200px; height: 576px; overflow: hidden; }
  body {
    position: relative;
    background: var(--backdrop);
    font-family: "Roboto", Arial, sans-serif;
  }

  .card {
    position: absolute;
    width: 484px;
    height: 293px;
    border-radius: 12px;
    overflow: hidden;
  }

  /* ---------- Front ---------- */
  .card--front {
    left: 82px; top: 139px;
    background: var(--brand-blue);
  }
  .front-brand {
    position: absolute;
    left: 0; right: 0; top: 64px;
    display: flex; align-items: center; justify-content: center; gap: 12px;
    color: var(--white);
  }
  .brand-square {
    width: 40px; height: 40px;
    background: var(--white);
    flex: none;
  }
  .brand-name {
    font-family: "Roboto", Arial, sans-serif;
    font-weight: 700;
    font-size: 26px;
    letter-spacing: 1px;
    text-transform: uppercase;
    line-height: 1;
    white-space: nowrap;
  }
  .services-band {
    position: absolute;
    left: 0; right: 0; top: 166px; height: 80px;
    background: linear-gradient(180deg, var(--silver-light), var(--silver));
    display: flex; flex-direction: column; justify-content: center; align-items: center;
    gap: 3px;
    color: var(--ink);
    font-size: 13.5px;
  }
  .services-band .sep { margin: 0 8px; }
  .front-web {
    position: absolute;
    left: 0; right: 0; top: 261px;
    display: flex; align-items: center; justify-content: center; gap: 18px;
    color: var(--silver-light);
    font-size: 12px;
  }
  .front-web .dash {
    width: 34px; height: 1px;
    background: var(--silver);
  }

  /* ---------- Back ---------- */
  .card--back {
    left: 602px; top: 138px;
    background: var(--paper);
  }
  .back-brand {
    position: absolute;
    right: 22px; top: 48px;
    display: flex; align-items: center; gap: 10px;
    color: var(--brand-blue);
  }
  .back-brand .brand-square { background: var(--brand-blue); width: 44px; height: 44px; }
  .back-brand .brand-name { font-size: 27px; }

  .name-tab {
    position: absolute;
    left: -16px; top: 135px;
    width: 32px; height: 32px;
    border-radius: 50%;
    background: var(--brand-blue);
  }
  .person {
    position: absolute;
    left: 19px; top: 138px; right: 22px;
  }
  .person-name {
    font-family: "Roboto Condensed", "Arial Narrow", sans-serif;
    font-weight: 700;
    font-size: 22px;
    color: var(--brand-blue);
    line-height: 1.1;
  }
  .person-role {
    display: flex; align-items: flex-end; gap: 4px;
    font-size: 12px;
    color: var(--ink-soft);
    margin-top: 2px;
  }
  .person-role .rule {
    flex: 1; height: 1px;
    background: var(--rule);
    margin-bottom: 3px;
  }

  .contact-list {
    position: absolute;
    left: 21px; top: 194px;
    list-style: none;
    font-size: 12.5px;
    color: var(--ink-soft);
  }
  .contact-list li {
    display: flex; align-items: center; gap: 10px;
    height: 17px;
  }
  .contact-list svg { width: 11px; height: 11px; fill: var(--brand-blue); flex: none; }
  .contact-list .accent { color: var(--brand-blue); }

  .address {
    position: absolute;
    right: 22px; top: 216px;
    text-align: right;
    font-size: 12.5px;
    font-style: normal;
    line-height: 17px;
    color: var(--ink-soft);
  }

  .back-footer-grey {
    position: absolute;
    left: 0; bottom: 0; width: 220px; height: 8px;
    background: var(--silver);
  }
  .tagline-band {
    position: absolute;
    right: 0; bottom: 0;
    width: 278px; height: 28px;
    background: var(--brand-blue);
    clip-path: polygon(12px 0, 100% 0, 100% 100%, 0 100%);
    color: var(--white);
    font-size: 12.5px;
    white-space: nowrap;
    display: flex; align-items: center; justify-content: flex-end;
    padding-right: 22px;
  }
</style>
</head>
<body>

<section class="card card--front" aria-label="Business card front">
  <div class="front-brand">
    <span class="brand-square" aria-hidden="true"></span>
    <span class="brand-name">BuildMark Solutions</span>
  </div>
  <div class="services-band">
    <p>New Software Implementations<span class="sep">|</span>Software Re-Implementations</p>
    <p>Redesigning Software Usage at the User Level</p>
    <p>Project Coordination &amp; Management<span class="sep">|</span>Continued Software Support</p>
  </div>
  <div class="front-web">
    <span class="dash"></span>
    <span>www.buildmark-solutions.example</span>
    <span class="dash"></span>
  </div>
</section>

<section class="card card--back" aria-label="Business card back">
  <div class="back-brand">
    <span class="brand-square" aria-hidden="true"></span>
    <span class="brand-name">BuildMark Solutions</span>
  </div>

  <span class="name-tab" aria-hidden="true"></span>
  <div class="person">
    <p class="person-name">Dana R. Whitfield</p>
    <p class="person-role"><span>Owner</span><span class="rule"></span></p>
  </div>

  <ul class="contact-list">
    <li>
      <svg viewBox="0 0 12 12" aria-hidden="true"><path d="M3 0h6a1 1 0 0 1 1 1v10a1 1 0 0 1-1 1H3a1 1 0 0 1-1-1V1a1 1 0 0 1 1-1zm0 1.5v8h6v-8zm3 8.6a.7.7 0 1 0 0 1.4.7.7 0 0 0 0-1.4z"/></svg>
      <span>555-201-4830</span>
    </li>
    <li>
      <svg viewBox="0 0 12 12" aria-hidden="true"><path d="M1 3.5C1 2 3 1.5 6 1.5s5 .5 5 2v1.2H8.2V3.6H3.8v1.1H1zM3 5.5h6l2 4.5v1H1v-1zm3 1.3a1.4 1.4 0 1 0 0 2.8 1.4 1.4 0 0 0 0-2.8z"/></svg>
      <span>800-555-0142 ext. 100</span>
    </li>
    <li>
      <svg viewBox="0 0 12 12" aria-hidden="true"><path d="M0 2h12v8H0zm1 1v.3l5 3.4 5-3.4V3zm0 1.5V9h10V4.5L6 7.9z"/></svg>
      <span>dana@buildmark-solutions.example</span>
    </li>
    <li>
      <svg viewBox="0 0 12 12" aria-hidden="true"><path d="M6 0a6 6 0 1 0 0 12A6 6 0 0 0 6 0zm0 1c.7 0 1.5 1.5 1.7 4H4.3C4.5 2.5 5.3 1 6 1zM3.3 5H1.1a5 5 0 0 1 3-3.7C3.7 2.2 3.4 3.5 3.3 5zm5.4 0c-.1-1.5-.4-2.8-.8-3.7a5 5 0 0 1 3 3.7zM1.1 6h2.2c.1 1.5.4 2.8.8 3.7a5 5 0 0 1-3-3.7zm3.2 0h3.4c-.2 2.5-1 4-1.7 4S4.5 8.5 4.3 6zm4.4 0h2.2a5 5 0 0 1-3 3.7c.4-.9.7-2.2.8-3.7z"/></svg>
      <span>www.<span class="accent">buildmark-solutions</span>.example</span>
    </li>
  </ul>

  <address class="address">
    14 Orchard Lane - Suite 210<br>
    Maple Falls, NY 10000
  </address>

  <span class="back-footer-grey" aria-hidden="true"></span>
  <div class="tagline-band">Planning Ahead - Building Better Systems</div>
</section>

</body>
</html>
```